Social Media App Needs PPT Template

We need a PowerPoint template for a new social media company based in the DC area called "Bold Ledger." We provide an interactive digital platform for executives to share actionable advice. We would like to see designs that use our orange logo color as an accent, but are mainly grey, white, and black. The final design should communicate clean, chic, modern, and professional.

Target Market(s)

Executives

Industry/Entity Type

Information Technology

Font styles to use
Sans Serif

Colors
f78f20
fbe7d2
ffffff
000000
e8e8e8
757575

Requirements
Must have
• My project must have title page and many options for the body of the ppt (graphs, tables, etc). It also needs to be easy to modify. I must have someone who is experienced in creating powerpoint templates.
Nice to have
• It would be nice to have a very modern and clean design that includes the logo on every page, but still leaves a lot of room for the content of the slide
Should not have
• My design project should not look to busy.

```html
<!DOCTYPE html>
<html lang="en">
<head>
<meta charset="utf-8">
<title>Bold Ledger – About Our Company</title>
<link href="https://fonts.googleapis.com/css2?family=Lato:wght@300;400;700&display=swap" rel="stylesheet">
<style>
  :root {
    --backdrop: #919191;
    --slide-bg: #f3f3f3;
    --orange: #f0931f;
    --orange-deep: #e6851a;
    --charcoal: #4a4a4a;
    --slate: #6d6d6f;
    --silver: #a8a8a8;
    --white: #ffffff;
  }
  * { margin: 0; padding: 0; box-sizing: border-box; }
  html, body { width: 1200px; height: 960px; overflow: hidden; }
  body {
    background: var(--backdrop);
    font-family: "Lato", sans-serif;
    position: relative;
  }
  .page-label {
    position: absolute; top: 45px; left: 0; width: 1200px;
    text-align: center; color: var(--white);
    font-weight: 300; font-size: 24px; letter-spacing: 0.5px;
  }
  .slide {
    position: absolute; left: 87px; top: 128px;
    width: 1046px; height: 784px;
    background: radial-gradient(ellipse at 50% 45%, #ffffff 0%, var(--slide-bg) 60%, #ededed 100%);
    overflow: hidden;
  }
  .slide-frame { position: absolute; left: 0; top: 0; width: 1046px; height: 784px; }
  .slide-title {
    position: absolute; left: 32px; top: 68px;
    color: var(--white); font-weight: 300; font-size: 40px;
  }
  .brand {
    position: absolute; left: 838px; top: 72px;
    display: flex; align-items: center; gap: 10px;
    color: var(--white); font-weight: 700; font-size: 26px;
  }
  .brand-dot { width: 22px; height: 22px; border-radius: 50%; background: var(--orange); }
  .stat-card {
    position: absolute; width: 355px; height: 190px; color: var(--white);
  }
  .stat-card--reach { left: 114px; top: 211px; background: var(--orange); }
  .stat-card--revenue { left: 616px; top: 211px; background: var(--slate); }
  .stat-card--savings { left: 114px; top: 477px; background: var(--charcoal); }
  .stat-card--growth { left: 616px; top: 477px; background: var(--silver); }
  .stat-figure {
    position: absolute; left: 85px; top: 26px;
    font-size: 38px; font-weight: 400; line-height: 1.1;
  }
  .stat-text {
    position: absolute; left: 83px; top: 78px;
    font-size: 17px; line-height: 21.6px;
  }
  .stat-icon {
    position: absolute; width: 116px; height: 116px; border-radius: 50%;
    border: 3px solid var(--white);
    display: flex; align-items: center; justify-content: center;
  }
  .stat-card--reach .stat-icon,
  .stat-card--savings .stat-icon { left: -58px; top: 41px; }
  .stat-card--revenue .stat-icon,
  .stat-card--growth .stat-icon { left: -54px; top: 41px; }
  .stat-card--reach .stat-icon { background: var(--orange); }
  .stat-card--revenue .stat-icon { background: var(--slate); }
  .stat-card--savings .stat-icon { background: var(--charcoal); }
  .stat-card--growth .stat-icon { background: var(--silver); }
  .stat-card--growth .stat-figure { top: 24px; }
  .stat-card--growth .stat-text { top: 75px; }
  .footer-text {
    position: absolute; left: 28px; top: 749px;
    color: #e4e4e4; font-size: 14px; font-weight: 400;
  }
</style>
</head>
<body>
  <div class="page-label">Page 11</div>

  <section class="slide">
    <svg class="slide-frame" viewBox="0 0 1307 980" preserveAspectRatio="none" aria-hidden="true">
      <polygon points="1019,43 1307,43 1307,55 1006,55" fill="var(--orange)"/>
      <polygon points="0,61 991,61 886,163 0,163" fill="var(--orange-deep)"/>
      <polygon points="700,61 991,61 935,116 0,116 0,140 650,140" fill="#f29a2c" opacity="0.45"/>
      <polygon points="1001,61 1307,61 1307,163 891,163" fill="var(--charcoal)"/>
      <polygon points="0,170 880,170 869,181 0,181" fill="var(--charcoal)"/>
      <polygon points="0,927 374,927 334,966 0,966" fill="var(--charcoal)"/>
      <polygon points="381,927 1307,927 1307,966 341,966" fill="var(--orange-deep)"/>
    </svg>

    <h1 class="slide-title">About Our Company</h1>
    <div class="brand"><span class="brand-dot"></span>Bold Ledger</div>

    <article class="stat-card stat-card--reach">
      <div class="stat-icon">
        <svg width="72" height="72" viewBox="0 0 72 72" fill="none" stroke="#fff" stroke-width="3.5" stroke-linejoin="round" stroke-linecap="round">
          <rect x="6" y="28" width="8" height="14"/>
          <polygon points="14,28 50,16 50,54 14,42"/>
          <rect x="50" y="13" width="6" height="44" rx="2"/>
          <path d="M22 45 v8 h12 v-5"/>
          <path d="M61 29 l6 -3 M62 35 h7 M61 41 l6 3"/>
        </svg>
      </div>
      <div class="stat-figure">915,456,459</div>
      <p class="stat-text">Lorem ipsum dolor sit amet,<br>consectetuer adipiscing elit, s<br>ed diam nonu mmy nibh euis<br>mod tincidunt</p>
    </article>

    <article class="stat-card stat-card--revenue">
      <div class="stat-icon">
        <svg width="72" height="72" viewBox="0 0 72 72" fill="none" stroke="#fff" stroke-width="3.5" stroke-linejoin="round" stroke-linecap="round">
          <path d="M26 6 h20 l-6 12 h-8 z"/>
          <path d="M30 18 h12"/>
          <path d="M30 21 C14 32 10 50 16 60 C20 66 52 66 56 60 C62 50 58 32 42 21 z"/>
          <text x="36" y="53" text-anchor="middle" fill="#fff" stroke="none" font-family="Lato, sans-serif" font-weight="700" font-size="24">$</text>
        </svg>
      </div>
      <div class="stat-figure">111,458,564</div>
      <p class="stat-text">Lorem ipsum dolor sit amet,<br>consectetuer adipiscing elit, s<br>ed diam nonu mmy nibh euis<br>mod tincidunt</p>
    </article>

    <article class="stat-card stat-card--savings">
      <div class="stat-icon">
        <svg width="72" height="72" viewBox="0 0 72 72">
          <ellipse cx="36" cy="44" rx="24" ry="16" fill="#fff"/>
          <rect x="18" y="52" width="8" height="12" rx="2" fill="#fff"/>
          <rect x="44" y="52" width="8" height="12" rx="2" fill="#fff"/>
          <rect x="8" y="40" width="8" height="9" rx="3" fill="#fff"/>
          <polygon points="20,34 18,24 28,30" fill="#fff"/>
          <circle cx="50" cy="14" r="9" fill="none" stroke="#fff" stroke-width="2.5"/>
          <text x="50" y="19" text-anchor="middle" fill="#fff" font-family="Lato, sans-serif" font-weight="700" font-size="13">$</text>
          <rect x="34" y="31" width="12" height="3" rx="1.5" fill="var(--charcoal)"/>
        </svg>
      </div>
      <div class="stat-figure">100%</div>
      <p class="stat-text">Lorem ipsum dolor sit amet,<br>consectetuer adipiscing elit, s<br>ed diam nonu mmy nibh euis<br>mod tincidunt</p>
    </article>

    <article class="stat-card stat-card--growth">
      <div class="stat-icon">
        <svg width="72" height="72" viewBox="0 0 72 72" fill="none" stroke="#fff" stroke-width="3.5" stroke-linejoin="round">
          <rect x="10" y="46" width="12" height="16"/>
          <rect x="22" y="36" width="12" height="26"/>
          <rect x="34" y="24" width="12" height="38"/>
          <rect x="46" y="12" width="12" height="50"/>
        </svg>
      </div>
      <div class="stat-figure">100%</div>
      <p class="stat-text">Lorem ipsum dolor sit amet,<br>consectetuer adipiscing elit, s<br>ed diam nonu mmy nibh euis<br>mod tincidunt</p>
    </article>

    <p class="footer-text">www.boldledger.com &nbsp;|&nbsp; Page 9</p>
  </section>
</body>
</html>
```